Business card design for holistic health care clinic

We need a double-sided business card design for our holistic health care clinic that integrates our logo design and also its color scheme. My business is called Valmira. It is an integrative medicine clinic. You have already done the logo for me. Please ensure an elegant and upscale design that is not cluttered, but still has all the necessary information (please see below for details).

Target Market(s)

Wellness, fitness, rehabilitation for educated, well-traveled open-minded clients who are focused on natural, organic, balanced and preventive healthcare and lifestyle.

Industry/Entity Type

Medical

Contact Information for Business Card

Modern, clean.

Number of Pages Required

1 page

Font styles to use
Serif
Sans Serif

Colors

Designer to choose colors to be used in the design.

Requirements
Must have
• Logo on one side, all other information on the other side.
• Other information should include:
• Tobias Wrenfeld - DOE, CPT, LMT
• 4100 East Marrow Drive
• Austin, TX 78119
• 512 555 0148
• 818 555 0192
• info@ValmiraHealth.example
• t.wrenfeld@ValmiraHealth.example
Nice to have
• Darker background on front - but not totally black - shaded/dark gray.

```html
<!DOCTYPE html>
<html lang="en">
<head>
<meta charset="utf-8">
<title>Valmira Business Card</title>
<link href="https://fonts.googleapis.com/css2?family=Nunito:wght@400;600;700;800;900&display=swap" rel="stylesheet">
<style>
  :root {
    --backdrop: #cfcfcf;
    --card-dark-top: #3b3c3e;
    --card-dark-bottom: #222324;
    --brand-blue: #0b93d0;
    --card-blue: #0a90cc;
    --ink-dark: #2a2b2e;
    --text-light: #f2f2f2;
  }
  * { margin: 0; padding: 0; box-sizing: border-box; }
  html, body {
    width: 1200px; height: 960px; overflow: hidden;
    background: var(--backdrop);
    font-family: "Nunito", sans-serif;
  }
  .canvas { position: relative; width: 1200px; height: 960px; }
  .card {
    position: absolute; width: 601px; height: 344px; border-radius: 20px;
    box-shadow: 2px 4px 6px rgba(0,0,0,0.35);
    overflow: hidden;
  }
  .card--front {
    left: 302px; top: 116px;
    background: linear-gradient(180deg, var(--card-dark-top), var(--card-dark-bottom));
  }
  .card--back { left: 299px; top: 501px; background: var(--card-blue); }

  .brand-name {
    position: absolute; font-weight: 900; letter-spacing: 0.5px; line-height: 1;
    text-transform: uppercase;
  }
  .card--front .brand-name { left: 36px; top: 70px; font-size: 50px; color: var(--brand-blue); }
  .brand-tagline { position: absolute; font-weight: 700; white-space: nowrap; }
  .card--front .brand-tagline { left: 40px; top: 117px; font-size: 16px; color: var(--brand-blue); }

  .address {
    position: absolute; left: 39px; top: 183px;
    font-size: 14px; line-height: 17px; color: var(--text-light);
  }
  .contact-list { position: absolute; left: 38px; top: 226px; list-style: none; }
  .contact-list li {
    display: flex; align-items: center; height: 19px;
    font-size: 14px; color: var(--text-light);
  }
  .contact-list svg { width: 14px; height: 14px; margin-right: 8px; fill: var(--brand-blue); }

  .holder { position: absolute; right: 41px; top: 222px; text-align: right; }
  .holder-name { font-size: 20px; font-weight: 800; color: var(--brand-blue); line-height: 1.1; }
  .holder-credentials { font-size: 11px; font-weight: 800; color: var(--brand-blue); letter-spacing: 0.4px; margin-top: 2px; }

  .card--back .brand-name {
    left: 0; right: 0; top: 130px; text-align: center;
    font-size: 66px; color: var(--ink-dark);
  }
  .card--back .brand-tagline {
    left: 0; right: 0; top: 197px; text-align: center;
    font-size: 19px; color: var(--ink-dark);
  }
  .motto {
    position: absolute; left: 0; right: 0; top: 279px;
    display: flex; justify-content: center; align-items: center;
    font-size: 15px; color: var(--ink-dark);
  }
  .motto::before, .motto::after {
    content: ""; width: 58px; height: 1px; background: var(--ink-dark); margin: 0 2px;
  }
</style>
</head>
<body>
<main class="canvas">
  <section class="card card--front" aria-label="Card front">
    <div class="brand-name">Valmira</div>
    <div class="brand-tagline">Integrative Holistic Medicine</div>
    <p class="address">4100 East Marrow Drive<br>Austin, TX 78119</p>
    <ul class="contact-list">
      <li><svg viewBox="0 0 24 24"><path d="M6.6 10.8a15.2 15.2 0 0 0 6.6 6.6l2.2-2.2a1 1 0 0 1 1-.25 11.4 11.4 0 0 0 3.6.57 1 1 0 0 1 1 1V20a1 1 0 0 1-1 1A17 17 0 0 1 3 4a1 1 0 0 1 1-1h3.5a1 1 0 0 1 1 1c0 1.25.2 2.45.57 3.57a1 1 0 0 1-.25 1z"/></svg>512 555 0148</li>
      <li><svg viewBox="0 0 24 24"><path d="M7 1h10a2 2 0 0 1 2 2v18a2 2 0 0 1-2 2H7a2 2 0 0 1-2-2V3a2 2 0 0 1 2-2zm0 3v14h10V4zm5 15.5a1.2 1.2 0 1 0 0 2.4 1.2 1.2 0 0 0 0-2.4z"/></svg>818 555 0192</li>
      <li><svg viewBox="0 0 24 24"><path d="M2 5h20v14H2zm2 2v.5l8 5.5 8-5.5V7l-8 5.5z"/></svg>t.wrenfeld@ValmiraHealth.example</li>
      <li><svg viewBox="0 0 24 24"><path d="M12 2a10 10 0 1 0 0 20 10 10 0 0 0 0-20zm-1 17.9A8 8 0 0 1 4.2 10l4.8 4.8v1a2 2 0 0 0 2 2zm6.9-2.5A2 2 0 0 0 16 16h-1v-3a1 1 0 0 0-1-1H8v-2h2a1 1 0 0 0 1-1V7h2a2 2 0 0 0 2-2v-.4a8 8 0 0 1 2.9 12.8z"/></svg>www.ValmiraHealth.example</li>
    </ul>
    <div class="holder">
      <div class="holder-name">TOBIAS WRENFELD</div>
      <div class="holder-credentials">DOE, CPT, LMT</div>
    </div>
  </section>

  <section class="card card--back" aria-label="Card back">
    <div class="brand-name">Valmira</div>
    <div class="brand-tagline">Integrative Holistic Medicine</div>
    <div class="motto">helping the body help itself</div>
  </section>
</main>
</body>
</html>
```